I would like to modify/update my 2 step login screen

I want a more modern looking login page for our document imaging application. I need to keep all of the same elements and buttons that currently exist. The first 2 screens are the login. The 3rd is a screenshot of the actual application home page.

```html
<!DOCTYPE html>
<html lang="en">
<head>
<meta charset="utf-8">
<title>Meridian Docs – Classic Login States</title>
<link href="https://fonts.googleapis.com/css2?family=Inter:wght@400;500;600;700&display=swap" rel="stylesheet">
<style>
:root{
  --page:#c2c3c5;
  --screen:#f6f6f6;
  --card:#ffffff;
  --ink:#1f1f1f;
  --muted:#8c8c8c;
  --faint:#b3b3b3;
  --line:#dcdcdc;
  --green:#52b35a;
  --disabled:#c6c6c6;
  --error:#e05858;
  --blue:#2f6fb3;
}
*{box-sizing:border-box;margin:0;padding:0}
html,body{width:1200px;height:482px;overflow:hidden;background:var(--page);font-family:'Inter',sans-serif;color:var(--ink)}
.board{position:absolute;left:0;top:0;width:2576px;height:1036px;transform:scale(.46584);transform-origin:0 0}
.screen{position:absolute;width:797px;height:448px;background:var(--screen)}
.card{position:absolute;left:119px;top:72px;width:559px;height:280px;background:var(--card);border-radius:14px;box-shadow:0 1px 4px rgba(0,0,0,.05);overflow:hidden}
.brand{position:absolute;left:28px;top:36px;display:flex;align-items:center;gap:8px;font-size:17px;font-weight:700;letter-spacing:.2px;color:var(--ink)}
.brand-mark{width:20px;height:20px;background:var(--ink);border-radius:3px}
.welcome{position:absolute;left:28px;top:204px;font-size:15px;font-weight:700}
.notice{position:absolute;left:28px;top:232px;font-size:6.5px;line-height:10px;color:#444}
.notice b{font-weight:600;color:var(--ink)}
.auth{position:absolute;left:280px;top:0;width:279px;height:280px;border-left:1px solid #f1f1f1}
.tabs{display:flex;height:35px;border-bottom:1px solid var(--line)}
.tab{flex:1;display:flex;align-items:center;justify-content:center}
.tab.active{border-bottom:2px solid var(--green);margin-bottom:-1px}
.tab svg{width:11px;height:11px}
.title{position:absolute;left:0;right:0;top:53px;text-align:center;font-size:14.5px;font-weight:600}
.field{position:absolute;left:37px;width:205px;height:26px;border:1px solid var(--line);border-radius:3px;display:flex;align-items:center;padding:0 7px;gap:6px;font-size:7.5px}
.field.focus{border-color:var(--green)}
.field.invalid{border-color:var(--error)}
.field .ico{width:10px;height:10px;flex:none;color:#444}
.field .placeholder{color:var(--faint)}
.field .value{color:var(--ink)}
.field .dots{font-size:10px;letter-spacing:1px;color:var(--ink)}
.caret{display:inline-block;width:1px;height:10px;background:var(--ink);vertical-align:middle;margin-left:1px}
.field .tools{margin-left:auto;display:flex;align-items:center;gap:5px;color:#999}
.field .tools svg{width:8px;height:8px}
.field .tools .sep{width:1px;height:10px;background:var(--line)}
.btn{position:absolute;left:37px;width:205px;height:23px;border-radius:3px;display:flex;align-items:center;justify-content:center;font-size:7.5px;font-weight:600;letter-spacing:.3px;color:#fff;background:var(--green)}
.btn.off{background:var(--disabled);color:#e9e9e9}
.error{position:absolute;left:0;right:0;text-align:center;font-size:6.5px;color:var(--error)}
.crumb{position:absolute;left:37px;width:205px;height:14px;display:flex;align-items:center;gap:8px;font-size:7.5px;color:var(--ink)}
.crumb svg{width:10px;height:10px;color:#777}
.crumb .sep{width:1px;height:11px;background:var(--line)}
.crumb b{font-weight:600}
.forgot{position:absolute;left:0;right:0;text-align:center;font-size:7.5px;font-weight:500;color:var(--green)}
.foot{position:absolute;left:133px;top:366px;width:531px;display:flex;justify-content:space-between;font-size:6.5px;color:var(--muted)}
.foot nav{display:flex;gap:6px;color:#333}
.foot nav i{font-style:normal;color:var(--faint)}
</style>
</head>
<body>
<svg width="0" height="0" style="position:absolute">
  <defs>
    <symbol id="i-lock" viewBox="0 0 12 12"><rect x="2" y="5.5" width="8" height="6" rx="1" fill="none" stroke="currentColor" stroke-width="1.1"/><path d="M4 5.5V3.8a2 2 0 0 1 4 0v1.7" fill="none" stroke="currentColor" stroke-width="1.1"/></symbol>
    <symbol id="i-lock-solid" viewBox="0 0 12 12"><rect x="2" y="5.5" width="8" height="6" rx="1" fill="currentColor"/><path d="M4 5.5V3.8a2 2 0 0 1 4 0v1.7" fill="none" stroke="currentColor" stroke-width="1.3"/></symbol>
    <symbol id="i-db" viewBox="0 0 12 12"><rect x="1.5" y="2" width="9" height="3.5" rx=".8" fill="none" stroke="currentColor" stroke-width="1"/><rect x="1.5" y="6.5" width="9" height="3.5" rx=".8" fill="none" stroke="currentColor" stroke-width="1"/></symbol>
    <symbol id="i-user" viewBox="0 0 12 12"><circle cx="6" cy="4" r="2.3" fill="none" stroke="currentColor" stroke-width="1"/><path d="M2 11c0-2.4 1.8-3.8 4-3.8s4 1.4 4 3.8" fill="none" stroke="currentColor" stroke-width="1"/></symbol>
    <symbol id="i-eye-off" viewBox="0 0 12 12"><path d="M1 6s2-3.5 5-3.5S11 6 11 6s-2 3.5-5 3.5S1 6 1 6z" fill="none" stroke="currentColor" stroke-width="1"/><circle cx="6" cy="6" r="1.5" fill="none" stroke="currentColor" stroke-width="1"/><path d="M2 10.5 10 1.5" stroke="currentColor" stroke-width="1"/></symbol>
    <symbol id="i-clear" viewBox="0 0 12 12"><circle cx="6" cy="6" r="5" fill="none" stroke="currentColor" stroke-width="1"/><path d="M4 4l4 4M8 4l-4 4" stroke="currentColor" stroke-width="1"/></symbol>
    <symbol id="i-back" viewBox="0 0 12 12"><path d="M10.5 6h-9M5 2.5 1.5 6 5 9.5" fill="none" stroke="currentColor" stroke-width="1"/></symbol>
  </defs>
</svg>

<div class="board">

  <!-- Step 1: empty -->
  <section class="screen" style="left:46px;top:46px">
    <div class="card">
      <div class="brand"><span class="brand-mark"></span>MERIDIAN DOCS</div>
      <h1 class="welcome">Welcome back!</h1>
      <p class="notice">All activity on this site is being recorded.<br>Your IP Address is being saved as '<b>192.168.168.134</b>'.</p>
      <div class="auth">
        <div class="tabs">
          <div class="tab active"><svg style="color:var(--blue)"><use href="#i-lock-solid"/></svg></div>
          <div class="tab"><svg viewBox="0 0 12 12"><circle cx="6" cy="6" r="4.5" fill="none" stroke="#e0463a" stroke-width="1.6"/></svg></div>
          <div class="tab"><svg viewBox="0 0 12 12"><rect x="1.5" y="1.5" width="9" height="9" fill="#6aa84f"/></svg></div>
          <div class="tab"><svg viewBox="0 0 12 12"><circle cx="6" cy="6" r="5" fill="#1a1a1a"/></svg></div>
        </div>
        <h2 class="title">Classic Login</h2>
        <div class="field" style="top:90px"><svg class="ico"><use href="#i-db"/></svg><span class="placeholder">Database</span></div>
        <div class="btn off" style="top:130px">NEXT</div>
      </div>
    </div>
    <footer class="foot"><span>Copyright 2007-2024 MD Meridian Docs</span><nav><span>Privacy</span><i>•</i><span>Remote Support</span><i>•</i><span>Contact Us</span></nav></footer>
  </section>

  <!-- Step 1: filled -->
  <section class="screen" style="left:890px;top:46px">
    <div class="card">
      <div class="brand"><span class="brand-mark"></span>MERIDIAN DOCS</div>
      <h1 class="welcome">Welcome back!</h1>
      <p class="notice">All activity on this site is being recorded.<br>Your IP Address is being saved as '<b>192.168.168.134</b>'.</p>
      <div class="auth">
        <div class="tabs">
          <div class="tab active"><svg style="color:var(--blue)"><use href="#i-lock-solid"/></svg></div>
          <div class="tab"><svg viewBox="0 0 12 12"><circle cx="6" cy="6" r="4.5" fill="none" stroke="#e0463a" stroke-width="1.6"/></svg></div>
          <div class="tab"><svg viewBox="0 0 12 12"><rect x="1.5" y="1.5" width="9" height="9" fill="#6aa84f"/></svg></div>
          <div class="tab"><svg viewBox="0 0 12 12"><circle cx="6" cy="6" r="5" fill="#1a1a1a"/></svg></div>
        </div>
        <h2 class="title">Classic Login</h2>
        <div class="field focus" style="top:90px"><svg class="ico"><use href="#i-db"/></svg><span class="value">ABC12345<span class="caret"></span></span><span class="tools"><svg><use href="#i-clear"/></svg></span></div>
        <div class="btn" style="top:130px">NEXT</div>
      </div>
    </div>
    <footer class="foot"><span>Copyright 2007-2024 MD Meridian Docs</span><nav><span>Privacy</span><i>•</i><span>Remote Support</span><i>•</i><span>Contact Us</span></nav></footer>
  </section>

  <!-- Step 1: invalid -->
  <section class="screen" style="left:1733px;top:46px">
    <div class="card">
      <div class="brand"><span class="brand-mark"></span>MERIDIAN DOCS</div>
      <h1 class="welcome">Welcome back!</h1>
      <p class="notice">All activity on this site is being recorded.<br>Your IP Address is being saved as '<b>192.168.168.134</b>'.</p>
      <div class="auth">
        <div class="tabs">
          <div class="tab active"><svg style="color:var(--blue)"><use href="#i-lock-solid"/></svg></div>
          <div class="tab"><svg viewBox="0 0 12 12"><circle cx="6" cy="6" r="4.5" fill="none" stroke="#e0463a" stroke-width="1.6"/></svg></div>
          <div class="tab"><svg viewBox="0 0 12 12"><rect x="1.5" y="1.5" width="9" height="9" fill="#6aa84f"/></svg></div>
          <div class="tab"><svg viewBox="0 0 12 12"><circle cx="6" cy="6" r="5" fill="#1a1a1a"/></svg></div>
        </div>
        <h2 class="title">Classic Login</h2>
        <div class="field invalid" style="top:90px"><svg class="ico"><use href="#i-db"/></svg><span class="value">ABC12345XYZ</span><span class="tools"><svg><use href="#i-clear"/></svg></span></div>
        <p class="error" style="top:123px">Invalid Database</p>
        <div class="btn" style="top:146px">NEXT</div>
      </div>
    </div>
    <footer class="foot"><span>Copyright 2007-2024 MD Meridian Docs</span><nav><span>Privacy</span><i>•</i><span>Remote Support</span><i>•</i><span>Contact Us</span></nav></footer>
  </section>

  <!-- Step 2: empty -->
  <section class="screen" style="left:46px;top:541px">
    <div class="card">
      <div class="brand"><span class="brand-mark"></span>MERIDIAN DOCS</div>
      <h1 class="welcome">Welcome back!</h1>
      <p class="notice">All activity on this site is being recorded.<br>Your IP Address is being saved as '<b>192.168.168.134</b>'.</p>
      <div class="auth">
        <div class="tabs">
          <div class="tab active"><svg style="color:var(--blue)"><use href="#i-lock-solid"/></svg></div>
          <div class="tab"><svg viewBox="0 0 12 12"><circle cx="6" cy="6" r="4.5" fill="none" stroke="#e0463a" stroke-width="1.6"/></svg></div>
          <div class="tab"><svg viewBox="0 0 12 12"><rect x="1.5" y="1.5" width="9" height="9" fill="#6aa84f"/></svg></div>
          <div class="tab"><svg viewBox="0 0 12 12"><circle cx="6" cy="6" r="5" fill="#1a1a1a"/></svg></div>
        </div>
        <h2 class="title">Classic Login</h2>
        <div class="crumb" style="top:90px"><svg><use href="#i-back"/></svg><span class="sep"></span><svg><use href="#i-db"/></svg><span>Database: <b>ABC12345</b></span></div>
        <div class="field" style="top:118px"><svg class="ico"><use href="#i-user"/></svg><span class="placeholder">Username</span></div>
        <div class="field" style="top:149px"><svg class="ico"><use href="#i-lock"/></svg><span class="placeholder">Password</span><span class="tools"><svg><use href="#i-eye-off"/></svg></span></div>
        <div class="btn off" style="top:189px">LOGIN</div>
        <p class="forgot" style="top:228px">Forgot Password?</p>
      </div>
    </div>
    <footer class="foot"><span>Copyright 2007-2024 MD Meridian Docs</span><nav><span>Privacy</span><i>•</i><span>Remote Support</span><i>•</i><span>Contact Us</span></nav></footer>
  </section>

  <!-- Step 2: filled -->
  <section class="screen" style="left:890px;top:541px">
    <div class="card">
      <div class="brand"><span class="brand-mark"></span>MERIDIAN DOCS</div>
      <h1 class="welcome">Welcome back!</h1>
      <p class="notice">All activity on this site is being recorded.<br>Your IP Address is being saved as '<b>192.168.168.134</b>'.</p>
      <div class="auth">
        <div class="tabs">
          <div class="tab active"><svg style="color:var(--blue)"><use href="#i-lock-solid"/></svg></div>
          <div class="tab"><svg viewBox="0 0 12 12"><circle cx="6" cy="6" r="4.5" fill="none" stroke="#e0463a" stroke-width="1.6"/></svg></div>
          <div class="tab"><svg viewBox="0 0 12 12"><rect x="1.5" y="1.5" width="9" height="9" fill="#6aa84f"/></svg></div>
          <div class="tab"><svg viewBox="0 0 12 12"><circle cx="6" cy="6" r="5" fill="#1a1a1a"/></svg></div>
        </div>
        <h2 class="title">Classic Login</h2>
        <div class="crumb" style="top:90px"><svg><use href="#i-back"/></svg><span class="sep"></span><svg><use href="#i-db"/></svg><span>Database: <b>ABC12345</b></span></div>
        <div class="field" style="top:118px"><svg class="ico"><use href="#i-user"/></svg><span class="value">JohnDoe123</span><span class="tools"><svg><use href="#i-clear"/></svg></span></div>
        <div class="field focus" style="top:149px"><svg class="ico"><use href="#i-lock"/></svg><span class="dots">●●●<span class="caret"></span></span><span class="tools"><svg><use href="#i-eye-off"/></svg><span class="sep"></span><svg><use href="#i-clear"/></svg></span></div>
        <div class="btn" style="top:189px">LOGIN</div>
        <p class="forgot" style="top:228px">Forgot Password?</p>
      </div>
    </div>
    <footer class="foot"><span>Copyright 2007-2024 MD Meridian Docs</span><nav><span>Privacy</span><i>•</i><span>Remote Support</span><i>•</i><span>Contact Us</span></nav></footer>
  </section>

  <!-- Step 2: invalid -->
  <section class="screen" style="left:1733px;top:541px">
    <div class="card">
      <div class="brand"><span class="brand-mark"></span>MERIDIAN DOCS</div>
      <h1 class="welcome">Welcome back!</h1>
      <p class="notice">All activity on this site is being recorded.<br>Your IP Address is being saved as '<b>192.168.168.134</b>'.</p>
      <div class="auth">
        <div class="tabs">
          <div class="tab active"><svg style="color:var(--blue)"><use href="#i-lock-solid"/></svg></div>
          <div class="tab"><svg viewBox="0 0 12 12"><circle cx="6" cy="6" r="4.5" fill="none" stroke="#e0463a" stroke-width="1.6"/></svg></div>
          <div class="tab"><svg viewBox="0 0 12 12"><rect x="1.5" y="1.5" width="9" height="9" fill="#6aa84f"/></svg></div>
          <div class="tab"><svg viewBox="0 0 12 12"><circle cx="6" cy="6" r="5" fill="#1a1a1a"/></svg></div>
        </div>
        <h2 class="title">Classic Login</h2>
        <div class="crumb" style="top:90px"><svg><use href="#i-back"/></svg><span class="sep"></span><svg><use href="#i-db"/></svg><span>Database: <b>ABC12345</b></span></div>
        <div class="field invalid" style="top:118px"><svg class="ico"><use href="#i-user"/></svg><span class="value">johndoe</span><span class="tools"><svg><use href="#i-clear"/></svg></span></div>
        <div class="field invalid" style="top:149px"><svg class="ico"><use href="#i-lock"/></svg><span class="dots">●●●●●●</span><span class="tools"><svg><use href="#i-eye-off"/></svg><span class="sep"></span><svg><use href="#i-clear"/></svg></span></div>
        <p class="error" style="top:182px">Invalid Username and/or Password</p>
        <div class="btn" style="top:205px">LOGIN</div>
        <p class="forgot" style="top:244px">Forgot Password?</p>
      </div>
    </div>
    <footer class="foot"><span>Copyright 2007-2024 MD Meridian Docs</span><nav><span>Privacy</span><i>•</i><span>Remote Support</span><i>•</i><span>Contact Us</span></nav></footer>
  </section>

</div>
</body>
</html>
```